Brindle Asset Management Vendor Recruiting Email

We need a digital flyer to email and post on Social media to attract new vendors to our website to apply to complete maintenance work on our clients homes. I have one flyer we had produced recently that we are un-happy with. It is attached.

The example given is what we do not want!! We do not want any of the pictures used from the existing one

Target Market(s)

Construction companies and handyman

Industry/Entity Type

Residential maintenance and repairs

Requirements
Must have
• Join our team as the header not become a vendor

```html
<!DOCTYPE html>
<html lang="en">
<head>
<meta charset="utf-8">
<title>Brindle Asset Management – Join Our Team</title>
<link rel="stylesheet" href="https://fonts.googleapis.com/css2?family=Montserrat:wght@400;600;700;800&family=Roboto:wght@400;500;700;900&display=swap">
<style>
  :root{
    --stage:#6a6a98;
    --night:#1b1928;
    --navy:#26286a;
    --purple:#a14fa0;
    --purple-soft:#b871b4;
    --violet-ink:#9d5aa7;
    --ink:#111217;
    --list-ink:#273461;
    --tile:#f5eef5;
    --cyan:#12c0ec;
    --white:#ffffff;
  }
  *{box-sizing:border-box;margin:0;padding:0}
  html,body{width:966px;height:1200px;overflow:hidden;background:var(--stage)}
  .flyer{position:absolute;left:94px;top:81px;width:779px;height:1011px;overflow:hidden;background:var(--white);font-family:"Roboto",sans-serif}
  .flyer-art{position:absolute;inset:0;width:779px;height:1011px}
  .brand{position:absolute;left:40px;top:128px;width:150px;text-align:center;color:var(--white);font-family:"Montserrat",sans-serif;font-weight:700}
  .brand-mark{display:block;width:14px;height:14px;margin:0 auto 8px;background:var(--white)}
  .brand-name{display:block;font-size:23px;letter-spacing:3px;line-height:1}
  .brand-sub{display:block;font-size:8.5px;letter-spacing:1.6px;margin-top:4px}
  .headline{position:absolute;left:38px;font-family:"Montserrat",sans-serif;font-weight:700;color:var(--white);line-height:1}
  .headline-join{top:198px;font-size:93px;letter-spacing:-3px}
  .headline-team{top:288px;font-size:199px;letter-spacing:-6px;font-weight:800}
  .req-band{position:absolute;left:52px;top:462px;width:420px;height:88px;padding:12px 0 0 20px;color:var(--white);font-family:"Montserrat",sans-serif;
    background:linear-gradient(180deg,var(--purple) 0%,var(--purple) 70%,var(--purple-soft) 100%);clip-path:polygon(0 0,372px 0,420px 88px,0 88px)}
  .req-title{font-size:36px;font-weight:700;letter-spacing:4.5px;line-height:1}
  .req-sub{font-size:20px;font-weight:400;letter-spacing:7.4px;margin-top:6px;line-height:1}
  .req-list{position:absolute;left:52px;top:549px;width:474px;height:130px;background:var(--white);clip-path:polygon(0 0,440px 0,474px 130px,0 130px)}
  .req-item{position:absolute;display:flex;gap:12px;font-size:13px;line-height:15px;color:var(--list-ink);letter-spacing:.3px}
  .tick{flex:none;width:11px;height:11px;margin-top:2px}
  .tile{position:absolute;background:var(--tile);color:var(--ink)}
  .tile-approval{left:52px;top:690px;width:215px;height:100px}
  .tile-volume{left:276px;top:690px;width:290px;height:100px;clip-path:polygon(0 0,250px 0,290px 100px,0 100px)}
  .tile-material{left:52px;top:799px;width:215px;height:101px}
  .tile-deposit{left:276px;top:799px;width:355px;height:101px;clip-path:polygon(0 0,312px 0,355px 101px,0 101px)}
  .icon{position:absolute}
  .stat{position:absolute;left:74px;top:16px;font-size:42px;font-weight:900;line-height:1}
  .note{position:absolute;font-size:11px;line-height:13px;font-weight:500}
  .tile-title{position:absolute;font-weight:700;line-height:1}
  .contact{position:absolute;left:64px;top:910px;display:flex;align-items:center;gap:12px}
  .call-label{font-family:"Montserrat",sans-serif;font-weight:700;font-size:19px;letter-spacing:3.3px;color:var(--ink)}
  .phone{font-family:"Montserrat",sans-serif;font-weight:700;font-size:35px;letter-spacing:1.5px;color:var(--violet-ink);margin-left:2px}
  .divider{position:absolute;left:64px;top:955px;width:508px;height:1px;background:var(--violet-ink)}
  .web{position:absolute;left:64px;top:964px;display:flex;align-items:center;gap:10px;font-family:"Montserrat",sans-serif;font-size:20px;letter-spacing:4.6px;color:var(--ink)}
  .accent-bar{position:absolute;left:0;top:1000px;width:696px;height:11px;background:linear-gradient(90deg,var(--purple) 0%,#8a68b4 35%,#4f98d8 60%,var(--cyan) 75%);clip-path:polygon(0 0,690px 0,696px 11px,0 11px)}
</style>
</head>
<body>
<main class="flyer">
  <svg class="flyer-art" viewBox="0 0 1399 1816" preserveAspectRatio="none" aria-hidden="false">
    <defs>
      <linearGradient id="night-fade" x1="0" y1="0" x2="0" y2="1">
        <stop offset="0" stop-color="#1b1928"/>
        <stop offset=".5" stop-color="#1f1c2c"/>
        <stop offset=".72" stop-color="#6d6a78"/>
        <stop offset=".85" stop-color="#f4f3f6"/>
        <stop offset="1" stop-color="#ffffff"/>
      </linearGradient>
      <linearGradient id="photo-tone" x1="0" y1="0" x2="1" y2="1">
        <stop offset="0" stop-color="#a9d8c9"/>
        <stop offset=".3" stop-color="#d9b98a"/>
        <stop offset=".55" stop-color="#2c3a84"/>
        <stop offset=".8" stop-color="#c99a6a"/>
        <stop offset="1" stop-color="#efe9e4"/>
      </linearGradient>
    </defs>
    <rect width="1399" height="1816" fill="url(#night-fade)"/>
    <polygon role="img" aria-label="Photo of a smiling tradesman in a hard hat holding a power drill on a building site" points="331,0 1399,0 1399,1816 1251,1816 941,1180" fill="url(#photo-tone)"/>
    <polygon points="761,0 1131,0 941,394" fill="#1b1928"/>
    <polygon points="560,640 941,1140 1180,740 1200,700 941,1200 540,660" fill="#26286a" opacity=".9"/>
    <polyline points="620,700 941,1130 1250,560" fill="none" stroke="#ffffff" stroke-width="5"/>
    <polyline points="1260,560 941,1200 1150,780" fill="none" stroke="#2d2f70" stroke-width="8"/>
  </svg>

  <div class="brand">
    <span class="brand-mark"></span>
    <span class="brand-name">BRINDLE</span>
    <span class="brand-sub">ASSET MANAGEMENT</span>
  </div>

  <h1 class="headline headline-join">JOIN OUR</h1>
  <div class="headline headline-team">TEAM</div>

  <section class="req-band">
    <h2 class="req-title">REQUIREMENTS</h2>
    <p class="req-sub">TO BECOME A VENDOR</p>
  </section>

  <ul class="req-list">
    <li class="req-item" style="left:23px;top:15px"><svg class="tick" viewBox="0 0 12 12"><rect x="0.5" y="0.5" width="11" height="11" fill="none" stroke="#1b1928" stroke-width="1.5"/><path d="M2.5 6l2.5 2.5L10 2" fill="none" stroke="#1b1928" stroke-width="2"/></svg>Auto insurance</li>
    <li class="req-item" style="left:23px;top:45px"><svg class="tick" viewBox="0 0 12 12"><rect x="0.5" y="0.5" width="11" height="11" fill="none" stroke="#1b1928" stroke-width="1.5"/><path d="M2.5 6l2.5 2.5L10 2" fill="none" stroke="#1b1928" stroke-width="2"/></svg><span>Certificate of<br>general liability<br>insurance</span></li>
    <li class="req-item" style="left:23px;top:98px"><svg class="tick" viewBox="0 0 12 12"><rect x="0.5" y="0.5" width="11" height="11" fill="none" stroke="#1b1928" stroke-width="1.5"/><path d="M2.5 6l2.5 2.5L10 2" fill="none" stroke="#1b1928" stroke-width="2"/></svg>Coverage area</li>
    <li class="req-item" style="left:174px;top:13px"><svg class="tick" viewBox="0 0 12 12"><rect x="0.5" y="0.5" width="11" height="11" fill="none" stroke="#1b1928" stroke-width="1.5"/><path d="M2.5 6l2.5 2.5L10 2" fill="none" stroke="#1b1928" stroke-width="2"/></svg><span>Workman's compensation or<br>state issued exemption letter</span></li>
    <li class="req-item" style="left:174px;top:55px"><svg class="tick" viewBox="0 0 12 12"><rect x="0.5" y="0.5" width="11" height="11" fill="none" stroke="#1b1928" stroke-width="1.5"/><path d="M2.5 6l2.5 2.5L10 2" fill="none" stroke="#1b1928" stroke-width="2"/></svg><span>Drive licence or state<br>issued ID card</span></li>
    <li class="req-item" style="left:174px;top:98px"><svg class="tick" viewBox="0 0 12 12"><rect x="0.5" y="0.5" width="11" height="11" fill="none" stroke="#1b1928" stroke-width="1.5"/><path d="M2.5 6l2.5 2.5L10 2" fill="none" stroke="#1b1928" stroke-width="2"/></svg>Any specialty licenses</li>
  </ul>

  <section class="tile tile-approval">
    <svg class="icon" style="left:21px;top:31px" width="35" height="35" viewBox="0 0 35 35"><circle cx="17.5" cy="17.5" r="15.5" fill="none" stroke="#111217" stroke-width="3"/><path d="M11 18l5 5 9-10" fill="none" stroke="#111217" stroke-width="3"/></svg>
    <p class="stat">95%</p>
    <p class="note" style="left:74px;top:62px">approval rating on all<br>submitted estimates.</p>
  </section>

  <section class="tile tile-volume">
    <p class="tile-title" style="left:13px;top:25px;font-size:24px">Guaranteed</p>
    <svg class="icon" style="left:158px;top:12px" width="44" height="38" viewBox="0 0 44 38"><g fill="none" stroke="#111217" stroke-width="2.5" stroke-linejoin="round"><path d="M22 3L41 12 22 21 3 12z"/><path d="M3 19l19 9 19-9"/><path d="M3 26l19 9 19-9"/></g></svg>
    <p class="tile-title" style="left:13px;top:56px;font-size:33px">Work Volume.</p>
  </section>

  <section class="tile tile-material">
    <svg class="icon" style="left:14px;top:32px" width="44" height="46" viewBox="0 0 44 46"><g fill="none" stroke="#111217" stroke-width="2.2"><path d="M2 8h28v36H2z"/><path d="M26 4h6v4"/><rect x="17" y="18" width="24" height="26" rx="2"/><rect x="21" y="22" width="16" height="5"/><path d="M22 31h3M28 31h3M34 31h3M22 35h3M28 35h3M34 35h3M22 39h3M28 39h3M34 39h3"/></g></svg>
    <p class="tile-title" style="left:74px;top:9px;font-size:19px;line-height:19px">Material<br>Purchasing<br>Program</p>
    <p class="note" style="left:74px;top:70px;font-size:9px;line-height:11px;font-weight:400">to help vendors with low capital<br>or no or bad credit.</p>
  </section>

  <section class="tile tile-deposit">
    <svg class="icon" style="left:13px;top:33px" width="58" height="42" viewBox="0 0 58 42"><g fill="none" stroke="#111217" stroke-width="2.4"><rect x="2" y="12" width="12" height="20"/><rect x="14" y="6" width="34" height="30" rx="2"/><rect x="20" y="2" width="36" height="38"/><circle cx="40" cy="20" r="5"/><path d="M14 30c6-2 8-12 14-14"/></g></svg>
    <p class="tile-title" style="left:95px;top:14px;font-size:25px;line-height:30px">Weekly Secure<br>Direct Deposit</p>
    <p class="note" style="left:95px;top:77px;font-size:14px;font-weight:400">with net 30 payment terms.</p>
  </section>

  <div class="contact">
    <svg width="18" height="18" viewBox="0 0 24 24"><path d="M6.6 10.8a15 15 0 006.6 6.6l2.2-2.2c.3-.3.7-.4 1-.2 1.1.4 2.3.6 3.6.6.6 0 1 .4 1 1V20c0 .6-.4 1-1 1A17 17 0 013 4c0-.6.4-1 1-1h3.5c.6 0 1 .4 1 1 0 1.3.2 2.5.6 3.6.1.3 0 .7-.2 1z" fill="#111217"/></svg>
    <span class="call-label">CALL US NOW!</span>
    <span class="phone">555-218-3090</span>
  </div>
  <div class="divider"></div>
  <div class="web">
    <svg width="20" height="20" viewBox="0 0 20 20"><g fill="none" stroke="#111217" stroke-width="1.3"><circle cx="10" cy="10" r="9"/><ellipse cx="10" cy="10" rx="4" ry="9"/><path d="M1 10h18M2.5 5.5h15M2.5 14.5h15"/></g></svg>
    <span>www.brindleassetmanagement.com</span>
  </div>

  <div class="accent-bar"></div>
</main>
</body>
</html>
```